Vennekamp.dk - FellowCup

I need a design for a WordPress site that serves to inform and present the national golfchampionship for colleagues in Denmark. The sites need to be visual stuninng or big, and it doesnt have a lot of pages. Maybe 5-6 regular text pages and not a lot of navigation. It should be a simple and powerfull site.

The sites need to present and sell the tournament, and have a clear call to action button "Sign up" (Tilmeld) and resultscoring.

If you can make a logo and visual ID for the tournament as well that would be a bonus.

Target Market(s)

Golfers

Logo Text

Vennekamp

Number of Pages Required

3 page

Requirements
Must have
• A frontpage
• Button 1 - Tilmeld (danish for sign up)
• Button 2 - Resultater (results)
Nice to have
• Logo
• A style we can use offline as well

```html
<!DOCTYPE html>
<html lang="da">
<head>
<meta charset="utf-8">
<title>Vennekamp 2015</title>
<link href="https://fonts.googleapis.com/css2?family=Roboto:wght@300;400;500;700&display=swap" rel="stylesheet">
<style>
:root{
  --green:#0b7d4e;
  --navy:#0d2a4f;
  --red:#b3163a;
  --blue:#1d5f9a;
  --gold:#d2a300;
  --ink:#333;
  --muted:#555;
  --page:#f3f3f3;
  --side:#4a4a4a;
  --side-dark:#3a3a3a;
  --dark:#222;
}
*{box-sizing:border-box;margin:0;padding:0}
html,body{width:1200px;height:2311px;overflow:hidden}
body{font-family:"Roboto",Arial,sans-serif;color:var(--ink);background:var(--page);position:relative;font-size:12px}
.wrap{position:absolute;left:98px;width:1004px}

.topbar{position:absolute;top:0;left:0;width:1200px;height:34px;background:#e6e6e6;font-size:12px;color:#666}
.topbar .contact{position:absolute;left:100px;top:10px;display:flex;gap:26px}
.topbar .account{position:absolute;right:100px;top:10px;display:flex;gap:18px}

.header{position:absolute;top:34px;left:0;width:1200px;height:128px;background:#fff}
.brand{position:absolute;left:100px;top:40px;display:flex;align-items:center;gap:12px}
.brand .dot{width:46px;height:46px;border-radius:50%;background:var(--green)}
.brand .name{font-size:20px;font-weight:500;color:#222;line-height:1.05;width:190px}
.mainnav{position:absolute;right:98px;top:50px;display:flex;gap:40px;font-size:12.5px;font-weight:500;text-transform:uppercase}
.mainnav a{text-decoration:none;padding-bottom:14px}
.mainnav .n1{color:#c9a000}
.mainnav .n2{color:var(--red);border-bottom:2px solid var(--red)}
.mainnav .n3{color:var(--blue)}
.mainnav .n4{color:var(--green)}

.subnav{position:absolute;top:162px;left:0;width:1200px;height:46px;background:#1f1f1f;display:flex;justify-content:space-between;padding:0 112px;align-items:center;color:#fff;font-size:14px}

.hero{position:absolute;top:208px;left:0;width:1200px;height:508px;background:linear-gradient(180deg,#2b3326 0%,#6b6a3a 35%,#c49a3a 55%,#6d7a3a 75%,#4d6a25 100%)}
.hero h1{position:absolute;left:98px;top:104px;font-weight:300;font-size:37px;color:#fff}
.hero p{position:absolute;left:98px;top:162px;width:585px;font-weight:300;font-size:23px;line-height:33px;color:#f2f2f2}
.btn{display:inline-block;background:var(--navy);color:#fff;text-decoration:none;font-size:17px;text-align:center}
.hero-cta{position:absolute;left:100px;top:284px;width:132px;height:44px;line-height:44px}
.dots{position:absolute;left:100px;top:367px;display:flex;gap:4px}
.dots i{width:10px;height:10px;border-radius:50%}
.search{position:absolute;left:98px;top:441px;display:flex;align-items:center;gap:22px;color:#fff;font-size:16px}
.search .field{height:38px;border:1px solid #ddd;background:rgba(0,0,0,.15);color:#fff;font-size:14px;padding:0 14px;display:flex;align-items:center;justify-content:space-between}
.search .kw{width:183px}
.search .sel{width:183px;background:rgba(40,40,40,.55)}
.search-btn{width:100px;height:38px;line-height:38px;margin-left:8px;font-size:16px}

.panel-title{height:46px;background:var(--green);color:#fff;font-size:19px;padding:12px 14px}
.side{background:var(--side);color:#fff;font-size:12.5px}
.menu li{list-style:none;height:29px;line-height:29px;padding-left:10px;border-bottom:1px solid #555}
.menu li::before{content:"»";margin-right:8px}
.menu li.on{background:var(--side-dark);color:var(--green);padding-left:20px}

.card{background:#fff;box-shadow:0 0 2px rgba(0,0,0,.1)}
.card-title{height:46px;border:1px solid #ddd;border-left:4px solid var(--green);font-size:20px;padding:11px 14px;color:#333;background:#fff}
.card-body{padding:22px 22px 14px;font-size:11.5px;line-height:25px;color:var(--muted)}
.card-body h3{color:var(--green);font-weight:400;font-size:15.5px;line-height:22px;margin:12px 0 4px}
.card-body .lead{font-weight:500;font-size:13.5px;line-height:24px;color:#444}

.docs .note{padding:8px 14px;font-size:12px;line-height:19px}
.doc{height:63px;display:flex;align-items:center;padding-left:14px;gap:32px;font-size:12.5px;line-height:19px}
.doc:nth-child(odd){background:var(--side-dark)}
.doc svg{flex:none}

.stops td{padding:0 10px 0 0;font-size:11.5px;line-height:23px}

.cta{position:absolute;top:1625px;left:98px;width:1004px;height:95px;background:var(--gold);color:#fff;font-size:12px;line-height:20px;padding:26px 20px}
.cta .btn{position:absolute;right:20px;top:24px;width:202px;height:46px;line-height:46px;font-size:16px}

.video{position:absolute;left:512px;top:0;width:492px;height:223px;background:linear-gradient(180deg,#5d7fa8 0%,#8a9aa5 45%,#5c6a4a 75%,#3b4530 100%)}
.video .bar{position:absolute;left:0;bottom:0;width:100%;height:22px;background:#222;display:flex;align-items:center;padding:0 8px;gap:10px}
.video .track{flex:1;height:4px;background:#666}
.video .track i{display:block;width:80%;height:100%;background:#ccc}

.partners{position:absolute;top:1993px;left:98px;width:1004px;height:123px;background:#fff;display:flex;justify-content:center;align-items:center;gap:64px;z-index:2;font-size:15px;font-weight:500}
.footer{position:absolute;top:2050px;left:0;width:1200px;height:261px;background:var(--dark);color:#bbb;text-align:center;font-size:12px}
.social{position:absolute;top:100px;left:0;width:100%;display:flex;justify-content:center;gap:18px}
.social i{width:16px;height:16px;border-radius:50%;background:#aaa}
.footer .line{position:absolute;left:0;width:100%}
.footer hr{position:absolute;top:210px;left:436px;width:480px;border:0;border-top:1px solid #444}
</style>
</head>
<body>

<div class="topbar">
  <div class="contact">
    <span>&#9742; +1 800 555 0142</span>
    <span>&#9993; mail@example.com</span>
  </div>
  <div class="account"><span>English ▾</span><span>Log in</span></div>
</div>

<header class="header">
  <div class="brand"><span class="dot"></span><span class="name">Nordlys Idrætsforbund</span></div>
  <nav class="mainnav">
    <a class="n1">Idræt og motion</a>
    <a class="n2">Arrangementer og stævner</a>
    <a class="n3">Sundhed på arbejdspladsen</a>
    <a class="n4">Foreningsnet</a>
  </nav>
</header>

<nav class="subnav">
  <span>Om Nordlys Idrætsforbund</span><span>Bliv medlem</span><span>Magasinet NORDLYS</span><span>Find forening</span><span>Pressecenter</span><span>Find person</span><span>Min side</span>
</nav>

<section class="hero" role="img" aria-label="Golfer swinging at sunset beside a lake, golf bag with clubs in the foreground">
  <h1>Vennekamp 2015</h1>
  <p>Find stævner og arrangementer f.eks. Nordlys Open, Løb og Cykel Stafet, Vinterløbet og foreningsarrangementer</p>
  <a class="btn hero-cta">Tilmeld</a>
  <div class="dots"><i style="background:#fff"></i><i style="background:var(--red)"></i><i style="background:var(--blue)"></i><i style="background:var(--green)"></i></div>
  <div class="search">
    <span>Find arrangement/stævne Søgeord</span>
    <span class="field kw">Søgeord</span>
    <span class="field sel">Vælg kommune <span>▾</span></span>
    <span class="field sel">Vælg tidspunkt <span>▾</span></span>
    <a class="btn search-btn">Søg</a>
  </div>
</section>

<aside class="wrap" style="top:741px;width:272px">
  <div class="panel-title">Arrangementer og stævner</div>
  <ul class="side menu" style="padding:6px 0 8px">
    <li class="on">Nordlys Open</li>
    <li>Løb &amp; Cykel Stafet</li>
    <li>Vinterløbet</li>
    <li>Kollegernes Aktivdag 2015</li>
    <li>Adventurerace</li>
    <li>Vennekamp</li>
    <li>Kollegabold</li>
    <li>NS Cup Fodbold</li>
    <li>NS Cup Høvdingebold</li>
    <li>Internetskydning</li>
    <li>Gokart</li>
    <li style="border:0">Arkiv</li>
  </ul>
</aside>

<article class="wrap card" style="top:741px;left:394px;width:708px;height:396px">
  <div class="card-title">Vær med, og vind rejsegavekort</div>
  <div class="card-body">
    <p class="lead">Vær med, og vind rejsegavekort for hele holdet på op til kr. 22.000,- som 1. præmie, dog max. kr. 5.500,- pr. deltager, jf. amatørbestemmelserne.Pris Kr. 500,- pr. hold.</p>
    <h3>Deltagere</h3>
    <p>Turneringen er åben for alle klubgolfere med gyldigt DGS-kort, gyldigt EHA handicap og amatørstatus.</p>
    <h3>Hold og puljer</h3>
    <p>Et hold består af 2-4 spillere med to spillere fra holdet pr. match. Turneringen kører i puljer á 5-6 hold, som er delt op geografisk, efter hvor i landet I kommer fra. Puljens holdkaptajner aftaler selv indbyrdes tid og sted for den enkelte match - så I kan spille, hvor og hvornår det passer jer.Alle betaler egen greenfee.</p>
    <h3>Spilleform</h3>
    <p>Spilleformen er en fourball - high/low hulspilsturnering, hvor 2 spillere fra holdet spiller med 2 spillere fra et andet hold. Læs mere i turneringsbetingelserne, som du finder her på siden.</p>
  </div>
</article>

<aside class="wrap docs" style="top:1183px;width:272px">
  <div class="panel-title">Mere information</div>
  <div class="side">
    <p class="note">Se resultaterne fra finalen her! NB: Klik på holdnavnet for en mere detaljeret score.</p>
    <div>
      <div class="doc"><svg width="28" height="34" viewBox="0 0 28 34"><path d="M0 0h20l8 8v26H0z" fill="#d9412b"/><path d="M20 0v8h8z" fill="#f08a78"/></svg><span>Puljer<br>(PDF, 203 KB)</span></div>
      <div class="doc"><svg width="28" height="34" viewBox="0 0 28 34"><path d="M0 0h20l8 8v26H0z" fill="#d9412b"/><path d="M20 0v8h8z" fill="#f08a78"/></svg><span>Turneringsplan<br>(PDF, 339 KB)</span></div>
      <div class="doc"><svg width="28" height="34" viewBox="0 0 28 34"><path d="M0 0h20l8 8v26H0z" fill="#d9412b"/><path d="M20 0v8h8z" fill="#f08a78"/></svg><span>Turneringsbetingelser<br>(PDF, 84 KB)</span></div>
      <div class="doc"><svg width="28" height="34" viewBox="0 0 28 34"><path d="M0 0h20l8 8v26H0z" fill="#d9412b"/><path d="M20 0v8h8z" fill="#f08a78"/></svg><span>Turneringsbetingelser<br>(PDF, 84 KB)</span></div>
      <div class="doc"><svg width="28" height="34" viewBox="0 0 28 34"><path d="M0 0h20l8 8v26H0z" fill="#d9412b"/><path d="M20 0v8h8z" fill="#f08a78"/></svg><span>Turneringsbetingelser<br>(PDF, 84 KB)</span></div>
    </div>
  </div>
</aside>

<article class="wrap card" style="top:1183px;left:394px;width:708px;height:420px">
  <div class="card-title">Finalestævne</div>
  <div class="card-body">
    <p>Vinderne fra hver pulje kvalificerer sig til at deltage i finalestævnet, som spilles på Egeskov Golfklub, Skovbrynet 12, 5400 Egeby fredag den 18. september 2015 kl. 10.00.Finalen bliver spillet som tableford four-ball best-ball med 7/8 handicap og med gunstart.Finalestævnet spilles af to spillere fra hvert hold. Greenfee og middag betales af Nordlys Idrætsforbund.</p>
    <h3>Præmier</h3>
    <p>Puljevindernes præmie er deltagelse i finalestævnet.Nordlys Idrætsforbund betaler greenfee, sportsbolle, vand og middag til finalestævnet.</p>
    <h3>Stopdatoer</h3>
    <table class="stops">
      <tr><td>Runde 1:</td><td>18. maj</td></tr>
      <tr><td>Runde 2:</td><td>8. juni</td></tr>
      <tr><td>Runde 3:</td><td>29. juni</td></tr>
      <tr><td>Runde 4:</td><td>17. august</td></tr>
      <tr><td>Runde 5:</td><td>7. september</td></tr>
    </table>
  </div>
</article>

<section class="cta">
  <p>Danmarks sjoveste kollegaturnering i golf. Spil mod andre spillere på nye baner.</p>
  <p><b>Tidspunkt:</b> 1. maj 2015 kl. 07:00 - 18. sep 2015 kl. 21:30 &nbsp;<b>Kontakt:</b> Mette Holm, Tlf. 65001234 &nbsp;<b>Tilmeldingsfrist:</b> 27. april 2015</p>
  <a class="btn">RESULTATER</a>
</section>

<section class="wrap" style="top:1745px;height:226px">
  <div style="width:490px">
    <div class="card-title">Finalepræmier</div>
    <div class="card-body" style="padding:16px 20px;line-height:22px">
      <ol style="padding-left:18px">
        <li>præmie: Et rejsegavekort på op til kr. 22.000,- pr. hold, dog max. kr. 5.500,- pr. tilmeldt spiller.</li>
        <li>præmie: Et gavekort til golfudstyr på kr. 2000,- pr. hold.</li>
        <li>præmie: Et gavekort til golfudstyr på kr. 1000,- pr. hold.</li>
      </ol>
      <p style="margin-top:4px">On the final day there is also prize for the longest drive and closest to the flag.</p>
    </div>
  </div>
  <div class="video" role="img" aria-label="Video interview with two tournament players on a golf course">
    <div class="bar">
      <svg width="10" height="10" viewBox="0 0 10 10"><path d="M1 0v10M9 0L3 5l6 5z" stroke="#ccc" fill="#ccc"/></svg>
      <svg width="10" height="10" viewBox="0 0 10 10"><rect x="1" y="0" width="3" height="10" fill="#ccc"/><rect x="6" y="0" width="3" height="10" fill="#ccc"/></svg>
      <span class="track"><i></i></span>
      <svg width="40" height="10" viewBox="0 0 40 10"><path d="M0 3h3l4-3v10l-4-3H0z" fill="#ccc"/><path d="M12 5h26" stroke="#ccc" stroke-width="3" stroke-dasharray="2 1"/></svg>
      <svg width="12" height="10" viewBox="0 0 12 10"><rect x="0.5" y="0.5" width="11" height="9" fill="none" stroke="#ccc"/></svg>
    </div>
  </div>
</section>

<section class="partners">
  <span style="color:var(--navy)"><span style="display:inline-block;width:14px;height:14px;border-radius:50%;background:var(--navy);vertical-align:middle;margin-right:6px"></span>Fjord Rejser</span>
  <span style="color:var(--green)">Dansk Golfsamvirke</span>
  <span style="display:inline-block;width:50px;height:50px;border-radius:50%;background:var(--red)"></span>
</section>

<footer class="footer">
  <div class="social"><i></i><i></i><i></i><i></i><i></i></div>
  <p class="line" style="top:140px">&#9679; Nordlys Idrætsforbund Havnevej 4 5800 Ringby ,</p>
  <p class="line" style="top:164px">&#9742; Tlf. 65 00 98 76 .</p>
  <p class="line" style="top:190px">&#9993; kontakt@nordlysidraet.dk</p>
  <hr>
  <p class="line" style="top:230px">© 2015 Nordlys Media ApS. Privacy policy</p>
</footer>

</body>
</html>
```